showcase project portfolio

create power point of project portfolio
from word file and website using similar design template

https://www.brelmor.co.uk/

Target Market(s)

corporte

```html
<!DOCTYPE html>
<html lang="en">
<head>
<meta charset="utf-8">
<title>Brelmor – Project Portfolio</title>
<link rel="stylesheet" href="https://fonts.googleapis.com/css2?family=Lexend:wght@300;400;500&family=Montserrat:wght@400;500;600;800&display=swap">
<style>
  :root {
    --stage: #646464;
    --paper: #ffffff;
    --navy: #1f3a52;
    --ink: #161616;
    --tan: #c9a58a;
    --tan-soft: #d8b9a2;
    --pill-shadow: rgba(0,0,0,0.10);
    --muted: #3a3a3a;
  }
  * { box-sizing: border-box; margin: 0; padding: 0; }
  html, body { width: 1041px; height: 1200px; overflow: hidden; background: var(--stage); }
  body { position: relative; font-family: "Montserrat", sans-serif; color: var(--ink); }

  .slide { position: absolute; width: 491px; height: 276px; background: var(--paper); overflow: hidden; }
  .col-left { left: 20px; } .col-right { left: 530px; }
  .row-1 { top: 25px; } .row-2 { top: 317px; } .row-3 { top: 608px; } .row-4 { top: 899px; }

  .abs { position: absolute; }
  .media { position: absolute; }

  .brand-mark { position: absolute; top: 9px; right: 12px; display: flex; align-items: center; gap: 3px;
    font-family: "Lexend", sans-serif; font-weight: 500; font-size: 8px; letter-spacing: 0.6px; color: var(--navy); }
  .brand-mark .dot { width: 5px; height: 5px; background: var(--tan); }
  .brand-mark.on-dark { color: var(--paper); }

  .tag { position: absolute; background: var(--tan); color: var(--paper); font-size: 4.4px; padding: 2px 5px; border-radius: 2px; font-family: "Montserrat", sans-serif; }
  .heading { position: absolute; font-family: "Lexend", sans-serif; font-weight: 400; font-size: 15px; color: var(--ink); line-height: 1.25; }
  .meta { position: absolute; font-size: 5px; color: var(--ink); }

  /* Welcome */
  .welcome-bg { inset: 0; background: linear-gradient(180deg, #f4f4f3 0%, #eeeeec 60%, #e6e8e2 100%); }
  .welcome-brand { left: 0; right: 0; top: 62px; text-align: center; font-family: "Lexend", sans-serif; font-weight: 500; font-size: 34px; letter-spacing: 6px; color: var(--navy); }
  .welcome-brand .dot { display: inline-block; width: 12px; height: 12px; background: var(--tan); margin-right: 10px; vertical-align: 4px; }
  .welcome-title { left: 0; right: 0; top: 182px; text-align: center; font-weight: 800; font-size: 28px; letter-spacing: 0.3px; color: var(--ink); }
  .welcome-tagline { left: 0; right: 0; top: 216px; text-align: center; font-weight: 600; font-size: 8.6px; color: var(--tan); letter-spacing: 0.2px; }

  /* Project 3 */
  .hero-band { left: 0; top: 0; width: 491px; height: 171px; background: linear-gradient(180deg, #2a2a28 0%, #3b3630 55%, #2c2f28 100%); }
  .hero-title { left: 0; right: 0; top: 59px; text-align: center; font-family: "Lexend", sans-serif; font-size: 15px; color: var(--paper); }
  .hero-sub { left: 0; right: 0; top: 81px; text-align: center; font-size: 7px; color: var(--paper); }
  .info-card { left: 30px; top: 127px; width: 431px; height: 122px; background: var(--paper); box-shadow: 0 2px 8px rgba(0,0,0,0.12); }
  .info-card .lines { position: absolute; left: 14px; top: 14px; width: 200px; font-size: 6.2px; line-height: 13px; color: var(--ink); }
  .info-card .row { display: flex; }
  .info-card .row span:first-child { width: 92px; }
  .plan-yellow { left: 218px; top: 17px; width: 200px; height: 82px; background: linear-gradient(90deg, #f3f1c6, #f6f4d4 50%, #eef0c8); border: 1px solid #cfcfcf; }

  /* Services */
  .services-title { left: 23px; top: 12px; font-family: "Lexend", sans-serif; font-size: 16px; line-height: 23px; color: var(--ink); }
  .pill { position: absolute; height: 16px; background: var(--paper); border-radius: 9px; box-shadow: 0 1px 4px var(--pill-shadow);
    display: flex; align-items: center; justify-content: space-between; padding: 0 3px 0 10px; font-size: 5.2px; font-weight: 500; text-transform: uppercase; color: var(--ink); line-height: 1.45; }
  .pill.tall { height: 23px; }
  .pill .num { flex: none; width: 9px; height: 9px; border-radius: 50%; background: var(--navy); color: var(--paper); font-size: 3.6px; display: flex; align-items: center; justify-content: center; margin-left: 4px; }
  .pill .num.tan { background: var(--tan); }
  .pill.left { left: 28px; width: 211px; }
  .pill.right { left: 251px; width: 211px; }

  /* Thank you */
  .thanks-brand { left: 0; right: 0; top: 48px; text-align: center; font-family: "Lexend", sans-serif; font-weight: 500; font-size: 28px; letter-spacing: 5px; color: var(--navy); }
  .thanks-brand .dot { display: inline-block; width: 10px; height: 10px; background: var(--tan); margin-right: 8px; vertical-align: 3px; }
  .thanks-title { left: 0; right: 0; top: 146px; text-align: center; font-family: "Lexend", sans-serif; font-weight: 400; font-size: 29px; letter-spacing: 1px; color: var(--ink); }
  .contact { position: absolute; top: 195px; display: flex; align-items: flex-start; gap: 6px; font-size: 5.8px; line-height: 10px; color: var(--ink); }
  .contact .icon { flex: none; width: 20px; height: 20px; border-radius: 50%; display: flex; align-items: center; justify-content: center; background: var(--navy); }
  .contact .icon.tan { background: var(--tan); }
  .contact .label { font-size: 7px; }
</style>
</head>
<body>

<!-- Welcome -->
<section class="slide col-left row-1">
  <div class="media welcome-bg" role="img" aria-label="Faded photograph of a white rendered house on a residential street"></div>
  <div class="abs welcome-brand"><span class="dot"></span>BRELMOR</div>
  <h1 class="abs welcome-title">WELCOME TO BRELMOR</h1>
  <p class="abs welcome-tagline">ARCHITECTURE TODAY, READY FOR TOMORROW</p>
</section>

<!-- Project 3 -->
<section class="slide col-right row-1">
  <div class="media hero-band" role="img" aria-label="Dusk photograph of a modern gabled house with large glazed windows"></div>
  <div class="brand-mark on-dark"><span class="dot"></span>BRELMOR</div>
  <span class="tag" style="left:232px;top:45px;">Project 3</span>
  <h2 class="abs hero-title">Location: 124 Fenwick Road, Derby</h2>
  <p class="abs hero-sub">Proposal: Change of use from offices (use class B1) to 12 flats (use class C3)</p>
  <div class="abs info-card">
    <div class="lines">
      <div class="row"><span>Location:</span><span>85-89 Carlow Street&nbsp;&nbsp; Derby</span></div>
      <div class="row"><span>Proposal:</span><span>Refurbishment Of Commercial</span></div>
      <div>Ground Floor Units Together With</div>
      <div style="white-space:nowrap;">Formation Of 6 Residential Units On First And Second Floors.</div>
      <div>Installation Of Glazing And</div>
      <div style="white-space:nowrap;">Repair To External Masonry Including Bricking Up Of Existing</div>
      <div>Openings</div>
    </div>
    <div class="media plan-yellow" role="img" aria-label="Floor plans of ground, first and second floors with flat layouts"></div>
  </div>
</section>

<!-- Services -->
<section class="slide col-left row-2">
  <div class="brand-mark"><span class="dot"></span>BRELMOR</div>
  <h2 class="abs services-title">Projects managed by Brelmor Design<br>Solutions Ltd</h2>

  <div class="pill left" style="top:80px;"><span>Creating working drawings</span><span class="num">01</span></div>
  <div class="pill left" style="top:104px;"><span>Price breakdown of total build costs</span><span class="num tan">02</span></div>
  <div class="pill left tall" style="top:129px;"><span>Liaising with Riverline Waters for water connection,<br>drainage connection</span><span class="num">03</span></div>
  <div class="pill left" style="top:161px;"><span>Liaising with Northway Gas to get gas supply to site</span><span class="num tan">04</span></div>
  <div class="pill left" style="top:184px;"><span>Liaising with Meridian Grid to get electric supply</span><span class="num">05</span></div>
  <div class="pill left" style="top:206px;"><span>Tendering out works to different tradesman</span><span class="num tan">06</span></div>
  <div class="pill left" style="top:228px;"><span>Getting material orders</span><span class="num">07</span></div>

  <div class="pill right" style="top:80px;"><span>Arranging structural engineer for the site</span><span class="num">08</span></div>
  <div class="pill right" style="top:104px;"><span>Arranging building control for the site</span><span class="num tan">09</span></div>
  <div class="pill right tall" style="top:129px;"><span>Making sure all tradesman work is up to current<br>British standards</span><span class="num">10</span></div>
  <div class="pill right" style="top:161px;"><span>Making sure material is on site on time</span><span class="num tan">11</span></div>
  <div class="pill right tall" style="top:184px;"><span>Daily walk rounds to check work is done according to<br>approved plans</span><span class="num">12</span></div>
  <div class="pill right" style="top:216px;"><span>Placing orders for bathrooms, kitchen, and flooring</span><span class="num tan">13</span></div>
  <div class="pill right" style="top:240px;"><span>All snag work with main contactor</span><span class="num">14</span></div>
</section>

<!-- Project 4 -->
<section class="slide col-right row-2">
  <div class="media" style="left:0;top:0;width:210px;height:276px;background:linear-gradient(180deg,#3d4f78 0%,#6b4a3a 45%,#4c3a2e 70%,#3d4a30 100%);" role="img" aria-label="Evening render of a large brick family house with lit windows and a landscaped garden"></div>
  <div class="brand-mark"><span class="dot"></span>BRELMOR</div>
  <span class="tag" style="left:246px;top:30px;">Project 4</span>
  <h2 class="heading" style="left:246px;top:41px;">Project 4</h2>
  <p class="meta" style="left:248px;top:64px;">Location:</p>
  <p class="meta" style="left:324px;top:64px;">Land At 1 Oakfield&nbsp;&nbsp; Derby&nbsp;&nbsp; DE23 4QX</p>
  <p class="meta" style="left:248px;top:75px;">Proposal:</p>
  <p class="meta" style="left:321px;top:75px;">Erection of a dwelling house (use class C3)</p>
  <div class="media" style="left:247px;top:99px;width:102px;height:55px;background:linear-gradient(180deg,#9aa6a8,#4f6b3a 50%,#6a6a62);" role="img" aria-label="Photo of the overgrown plot before building"></div>
  <div class="media" style="left:358px;top:99px;width:85px;height:55px;background:linear-gradient(180deg,#8fb0d0,#8a5a48 50%,#6f6a66);" role="img" aria-label="Photo of the completed brick house"></div>
  <div class="media" style="left:247px;top:166px;width:102px;height:78px;background:linear-gradient(135deg,#f6f6ef,#eeeed8 60%,#f6f6f2);border:1px solid #e2e2e2;" role="img" aria-label="Floor plans and site plan drawings"></div>
  <div class="media" style="left:358px;top:166px;width:100px;height:78px;background:linear-gradient(180deg,#ffffff 0%,#6d6d6d 25%,#8a5a4a 60%,#ffffff 100%);" role="img" aria-label="Proposed front elevation drawing with notes"></div>
</section>

<!-- Project one -->
<section class="slide col-left row-3">
  <div class="brand-mark"><span class="dot"></span>BRELMOR</div>
  <div class="media" style="left:28px;top:33px;width:201px;height:210px;border-radius:8px;background:linear-gradient(160deg,#6a3a2c 0%,#7a5040 40%,#4f5a3a 70%,#5d6a4a 100%);" role="img" aria-label="Photo of old brick garages with wooden doors"></div>
  <span class="tag" style="left:248px;top:46px;">Project one</span>
  <h2 class="heading" style="left:248px;top:57px;">Garages at Ashcombe Mews,<br>Ashcombe Street, Derby</h2>
  <p class="meta" style="left:249px;top:102px;width:225px;line-height:10.5px;">Proposal: Change of use from garages to two dwelling houses (use class C3) including alterations to the front and side elevations</p>
  <div class="media" style="left:249px;top:134px;width:112px;height:93px;background:linear-gradient(180deg,#f4ef7a 0%,#f4f1a8 35%,#f4f4f4 55%,#ffffff 100%);box-shadow:0 1px 4px rgba(0,0,0,0.12);" role="img" aria-label="Plans and elevations for the garage conversion"></div>
  <div class="media" style="left:369px;top:135px;width:77px;height:63px;background:linear-gradient(135deg,#3c2e2a,#7a5a4a 55%,#8aa07a);" role="img" aria-label="Photo of the converted mews houses"></div>
</section>

<!-- Project 5 -->
<section class="slide col-right row-3">
  <div class="brand-mark"><span class="dot"></span>BRELMOR</div>
  <span class="tag" style="left:29px;top:30px;">Project 5</span>
  <h2 class="heading" style="left:29px;top:41px;">Project 5</h2>
  <p class="meta" style="left:31px;top:64px;">Location: 27, Lindell Street, Birmingham</p>
  <p class="meta" style="left:31px;top:75px;">Proposal: Warehouse conversion to 4 town houses.</p>
  <div class="media" style="left:291px;top:14px;width:84px;height:113px;background:linear-gradient(180deg,#4a7ac0 0%,#8a5a4a 35%,#7a4a3a 70%,#7a7a7a 100%);" role="img" aria-label="Photo of the warehouse rear courtyard"></div>
  <div class="media" style="left:34px;top:105px;width:122px;height:139px;background:linear-gradient(180deg,#7a4232,#8a5040 60%,#6e6e70);" role="img" aria-label="Photo of the warehouse street frontage before conversion"></div>
  <div class="media" style="left:166px;top:105px;width:107px;height:140px;background:linear-gradient(180deg,#7a3e30,#86483a 55%,#e8e4de);" role="img" aria-label="Photo of the converted frontage"></div>
  <div class="media" style="left:289px;top:138px;width:156px;height:121px;background:linear-gradient(90deg,#ffffff,#f4f4ea 30%,#ffffff 55%,#f2f2e6 80%,#ffffff);box-shadow:0 1px 4px rgba(0,0,0,0.12);" role="img" aria-label="Floor plans of the four town houses"></div>
</section>

<!-- Project 2 -->
<section class="slide col-left row-4">
  <div class="brand-mark"><span class="dot"></span>BRELMOR</div>
  <span class="tag" style="left:230px;top:42px;">Project 2</span>
  <h2 class="heading" style="left:0;right:0;top:58px;text-align:center;">Location: 124 Fenwick Road, Derby</h2>
  <p class="meta" style="left:0;right:0;top:81px;text-align:center;font-size:6.8px;">Proposal: Change of use from offices (use class B1) to 12 flats (use class C3)</p>
  <div class="media" style="left:37px;top:109px;width:205px;height:122px;background:linear-gradient(180deg,#4f6a3a 0%,#8a5040 45%,#9a9a94 100%);" role="img" aria-label="Photo of the office building behind a large tree"></div>
  <div class="media" style="left:249px;top:109px;width:203px;height:122px;background:linear-gradient(180deg,#5a7040 0%,#8a5a46 45%,#b0aca4 100%);" role="img" aria-label="Photo of the building front and driveway"></div>
</section>

<!-- Thank you -->
<section class="slide col-right row-4">
  <div class="abs thanks-brand"><span class="dot"></span>BRELMOR</div>
  <h2 class="abs thanks-title">THANK YOU</h2>
  <div class="contact" style="left:101px;">
    <span class="icon"><svg width="9" height="11" viewBox="0 0 9 11"><path d="M4.5 0.5a3.5 3.5 0 0 0-3.5 3.5c0 2.6 3.5 6.5 3.5 6.5s3.5-3.9 3.5-6.5a3.5 3.5 0 0 0-3.5-3.5z" fill="#fff"/><circle cx="4.5" cy="4" r="1.3" fill="#1f3a52"/></svg></span>
    <span>Business Centre<br>Elmstead Road Village,<br>Harwood, Derby DE22 7PL</span>
  </div>
  <div class="contact" style="left:223px;">
    <span class="icon tan"><svg width="10" height="10" viewBox="0 0 10 10"><path d="M2.2 0.8l1.6 1.9-0.9 1.3c0.6 1.3 1.6 2.3 2.9 2.9l1.3-0.9 1.9 1.6-0.7 1.4C4.6 8.9 1.1 5.4 0.8 1.5z" fill="#fff"/></svg></span>
    <span><span class="label">PHONE</span><br>+447700900123</span>
  </div>
  <div class="contact" style="left:314px;">
    <span class="icon"><svg width="10" height="8" viewBox="0 0 10 8"><rect x="0.5" y="0.5" width="9" height="7" rx="1" fill="#fff"/><path d="M0.8 1l4.2 3.2L9.2 1" stroke="#1f3a52" stroke-width="0.9" fill="none"/></svg></span>
    <span><span class="label">EMAIL</span><br>info@brelmor.co.uk</span>
  </div>
</section>

</body>
</html>
```